furniture and home contents restoration

I need to list the services that we perform in our studio.
we serve the general public as well as the insurance/ remediation industry

```html
<!DOCTYPE html>
<html lang="en">
<head>
<meta charset="utf-8">
<title>Keystone Refinishers – Business Card</title>
<link href="https://fonts.googleapis.com/css2?family=Noto+Serif:wght@400;700&display=swap" rel="stylesheet">
<style>
  :root {
    --page-bg: #d6d6d6;
    --card-bg: #21323b;
    --ink: #ffffff;
  }
  * { margin: 0; padding: 0; box-sizing: border-box; }
  html, body { width: 1200px; height: 965px; overflow: hidden; }
  body { background: var(--page-bg); font-family: "Noto Serif", Georgia, serif; color: var(--ink); position: relative; }

  .card { position: absolute; top: 159px; width: 383px; height: 668px; background: var(--card-bg); }
  .card--front { left: 186px; }
  .card--back { left: 653px; }

  .abs { position: absolute; left: 0; right: 0; text-align: center; white-space: nowrap; }

  .brand { font-weight: 700; text-transform: uppercase; line-height: 50px; letter-spacing: 0.5px; }
  .card--front .brand { top: 30px; font-size: 40px; }
  .card--back .brand { top: 24px; font-size: 44px; line-height: 54px; }

  .person { top: 292px; font-size: 23px; font-weight: 700; letter-spacing: 0.3px; }

  .icon-row { top: 355px; height: 20px; }
  .icon-row svg { display: block; }

  .contact { top: 390px; font-size: 17px; line-height: 22.8px; }
  .rule { position: absolute; height: 2px; background: var(--ink); }
  .card--front .rule { top: 521px; left: 45px; width: 294px; }
  .tagline { top: 538px; font-size: 16.5px; line-height: 23px; }
  .specialty { top: 615px; font-size: 17px; text-transform: uppercase; }

  .services { position: absolute; left: 34px; list-style: none; font-size: 14px; line-height: 17.8px; text-transform: uppercase; white-space: nowrap; }
  .services li::before { content: "•"; margin-right: 4px; }
  .services--a { top: 170px; }
  .services--b { top: 377px; }
  .card--back .rule { top: 572px; left: 35px; width: 312px; }
  .assessment { position: absolute; left: 35px; top: 592px; font-size: 12.4px; line-height: 16px; text-transform: uppercase; }
</style>
</head>
<body>
  <section class="card card--front">
    <h1 class="abs brand">Keystone<br>Refinishers</h1>
    <p class="abs person">DANIEL MARCONI</p>
    <div class="abs icon-row">
      <svg width="383" height="20" viewBox="0 0 383 20">
        <path d="M34 10 Q80 8 113 9 L113 11 Q80 11 34 10Z" fill="#fff"/>
        <path d="M269 9 Q310 9 348 10 Q310 11 269 11Z" fill="#fff"/>
        <g fill="#fff">
          <rect x="125" y="0" width="20" height="20"/>
          <rect x="153" y="0" width="20" height="20"/>
          <rect x="181" y="0" width="20" height="20"/>
          <rect x="209" y="0" width="20" height="20"/>
          <rect x="238" y="0" width="20" height="20"/>
        </g>
        <g fill="none" stroke="#21323b" stroke-width="1.5">
          <path d="M130 4 Q129 11 137 16 L139 14 L137 12 L135 13 Q132 10 132 7 L134 6 L132 4Z"/>
          <rect x="159" y="3.5" width="8" height="13" rx="1"/>
          <rect x="186" y="8" width="10" height="6"/>
          <rect x="188" y="4" width="6" height="4"/>
          <rect x="188" y="12" width="6" height="4"/>
          <rect x="213" y="5" width="12" height="10"/>
          <path d="M213 5 L219 10 L225 5"/>
        </g>
        <path d="M248 3 A5 5 0 0 1 253 8 Q253 11 248 17 Q243 11 243 8 A5 5 0 0 1 248 3Z" fill="#21323b"/>
        <circle cx="248" cy="8" r="1.8" fill="#fff"/>
      </svg>
    </div>
    <address class="abs contact" style="font-style:normal">
      555 210 4400<br>555 318 7294<br>555 210 4460<br>k4stone@mailbox.com<br>28 brook valley rd. harlow, ny 10990
    </address>
    <div class="rule"></div>
    <p class="abs tagline">serving the general public and the<br>insurance industry for over 40 years</p>
    <p class="abs specialty">Home Contents Restoration</p>
  </section>

  <section class="card card--back">
    <h2 class="abs brand">Keystone<br>Refinishers</h2>
    <ul class="services services--a">
      <li>Antique repair and restoration</li>
      <li>Art cleaning and remounting</li>
      <li>Art and mirror frame repair</li>
      <li>Chandelier cleaning and restoration</li>
      <li>Document restoration</li>
      <li>Glass, ceramic, and mirror repair</li>
      <li>Hardware repair and restoration</li>
      <li>Kitchen removal and reinstallation</li>
      <li>Lamp cleaning and restoration</li>
      <li>Lamp shade replacement</li>
    </ul>
    <ul class="services services--b">
      <li>Metal polishing and restoration</li>
      <li>Odor removal and ozone services</li>
      <li>Photo restoration</li>
      <li>Upholstery cleaning and deodorizing</li>
      <li>In-house upholstery and reupholstery</li>
      <li>Rug cleaning and restoration</li>
      <li>Musical instrument restoration</li>
      <li>Window treatment repair/ restoration</li>
      <li>Leather restoration and replacement</li>
      <li>Piano restoration and repair</li>
    </ul>
    <div class="rule"></div>
    <p class="assessment">On-site inspections and desk review services<br>Assessment reports and estimates for repair<br>and restoration</p>
  </section>
</body>
</html>
```